Cannabis & Shroom Informative

Online Blog/Informative website design
Example site: https://leafharborshop.com/

I will need the Ad space as well.

Target Market(s)

Cannabis and (psyho) Mushroom Users

Number of Pages Required

1 page

Colors

Designer to choose colors to be used in the design.

```html
<!DOCTYPE html>
<html lang="en">
<head>
<meta charset="utf-8">
<title>Verdant Notes</title>
<link href="https://fonts.googleapis.com/css2?family=Montserrat:wght@500;600;700&family=Lato:wght@400;700&display=swap" rel="stylesheet">
<style>
:root{
  --green:#8cb83f;
  --green-dark:#6f9a2a;
  --green-pale:#b9d67f;
  --ink:#222;
  --text:#777;
  --dark:#2a2a2a;
  --white:#fff;
  --line:#e6e6e6;
}
*{box-sizing:border-box;margin:0;padding:0}
html,body{width:1200px;height:3477px;overflow:hidden;background:var(--white)}
body{position:relative;font-family:'Lato',sans-serif;color:var(--ink)}
a{text-decoration:none;color:inherit}

/* header */
.site-header{position:absolute;left:0;top:0;width:1200px;height:74px;background:var(--white);z-index:3}
.brand{position:absolute;left:118px;top:-8px;width:158px;height:158px;border-radius:50%;background:var(--white);z-index:4;display:flex;align-items:center;justify-content:center;text-align:center;font-family:'Montserrat',sans-serif;font-weight:600;font-size:17px;line-height:1.15;color:var(--ink)}
.main-nav{position:absolute;right:110px;top:30px;display:flex;gap:36px;font-size:14.5px;font-weight:700;color:var(--ink);text-transform:uppercase}
.main-nav .current{color:var(--green);position:relative}
.main-nav .current::after{content:"";position:absolute;left:0;right:0;bottom:-12px;height:3px;background:var(--green)}

/* hero */
.hero{position:absolute;left:0;top:74px;width:1200px;height:558px;overflow:hidden}
.hero-photo{position:absolute;inset:0;background:radial-gradient(ellipse at 25% 20%,#f3b54a 0%,#c7872c 30%,#6f5a25 60%,#364a1f 100%)}
.hero-photo::after{content:"";position:absolute;left:0;right:0;bottom:0;height:170px;background:linear-gradient(180deg,rgba(90,50,20,0) 0%,#5a3a1e 70%)}
.hero-title{position:absolute;left:118px;top:160px;font-family:'Montserrat',sans-serif;font-weight:600;font-size:58px;color:var(--white);letter-spacing:1px}
.hero-lead{position:absolute;left:118px;top:248px;width:510px;font-size:14.5px;line-height:26px;color:var(--white)}
.btn{display:inline-flex;align-items:center;gap:8px;background:var(--green);color:var(--white);font-weight:700;font-size:14.5px;text-transform:uppercase;border-radius:30px}
.hero .btn{position:absolute;left:118px;top:332px;height:54px;padding:0 22px}
.btn-ico{width:14px;height:14px}
.dots{position:absolute;left:573px;top:494px;display:flex;gap:3px}
.dots i{width:9px;height:9px;border-radius:50%;background:var(--white);display:block}
.dots i.on{background:transparent;border:2px solid var(--white)}

/* deal cards */
.deal{position:absolute;top:733px;width:316px;height:240px;box-shadow:0 0 6px rgba(0,0,0,.18);border:4px solid var(--white)}
.deal-photo{position:absolute;inset:0}
.deal-label{position:absolute;left:0;right:0;bottom:30px;text-align:center;color:var(--white);font-weight:700;font-size:14.5px;text-transform:uppercase;display:flex;justify-content:center;align-items:center;gap:8px}
.deal.active .frame{position:absolute;inset:6px;border:3px solid var(--white)}

/* info row */
.panel{position:absolute;top:1065px;width:236px;height:412px;box-shadow:0 0 6px rgba(0,0,0,.2);border:3px solid var(--white);color:var(--white);text-align:center}
.panel-photo{position:absolute;inset:0;background:linear-gradient(180deg,#3a3a36 0%,#2b2f28 60%,#4a5a30 100%)}
.panel-body{position:relative;padding:0 18px}
.panel h2{font-family:'Montserrat',sans-serif;font-weight:600;font-size:30px;line-height:36px}
.panel p{font-size:14.5px;line-height:29px;margin-top:14px}
.panel .btn{height:44px;padding:0 16px;margin-top:16px}

.post{position:absolute;width:236px}
.post-photo{height:200px;border:3px solid var(--white);box-shadow:0 0 6px rgba(0,0,0,.2);position:relative}
.post-date{position:absolute;right:12px;top:12px;width:50px;height:48px;background:var(--green);color:var(--white);font-weight:700;font-family:'Montserrat',sans-serif;font-size:14px;line-height:19px;text-align:center;padding-top:5px}
.post h3{font-weight:700;font-size:14.5px;margin:26px 0 0 16px;text-transform:uppercase}
.post .rule{width:55px;height:3px;background:var(--green);margin:14px 0 0 16px}
.post p{font-size:14.5px;line-height:25.5px;color:var(--text);margin:14px 0 0 16px}
.read{display:inline-flex;align-items:center;gap:8px;color:var(--green);font-weight:700;font-size:14.5px;text-transform:uppercase;margin:12px 0 0 16px}

/* promo banner */
.promo{position:absolute;left:112px;top:1636px;width:978px;height:181px}

/* trending */
.trending{position:absolute;left:877px;top:1962px;width:213px}
.trending h2{font-family:'Montserrat',sans-serif;font-weight:500;font-size:24px;color:var(--ink)}
.trend{display:flex;align-items:center;height:193px}
.trend:first-of-type{margin-top:22px}
.trend-photo{width:80px;height:80px;border-radius:50%;border:4px solid var(--white);box-shadow:0 0 6px rgba(0,0,0,.25);flex:none}
.trend-text{flex:1;text-align:center;font-size:17px;line-height:27.5px;color:var(--ink)}
.trend-text small{display:block;font-size:11.5px;color:var(--text);margin-top:6px}

/* pagination */
.pager{position:absolute;left:364px;top:3060px;width:201px;height:60px;box-shadow:0 0 6px rgba(0,0,0,.2);display:flex;align-items:center;padding-left:14px;font-size:14.5px;color:#555}
.pager span{width:36px;text-align:center;border-right:1px solid var(--line)}
.pager .next{border:none;width:auto;margin-left:30px}

/* footer */
.site-footer{position:absolute;left:0;top:3208px;width:1200px;height:269px;background:radial-gradient(ellipse at 50% 40%,#4b5a31 0%,#2f3a22 55%,#1f2618 100%);color:var(--white);text-align:center}
.social{position:absolute;left:518px;top:75px;display:flex;gap:10px}
.social i{display:block;width:34px;height:34px;border-radius:50%;border:2px solid var(--white)}
.foot-nav{position:absolute;left:0;right:0;top:142px;display:flex;justify-content:center;gap:28px;font-weight:700;font-size:14.5px;text-transform:uppercase}
.copy{position:absolute;left:0;right:0;top:191px;font-size:13.5px}
</style>
</head>
<body>

<header class="site-header">
  <nav class="main-nav">
    <a class="current">Home</a><a>About Us</a><a>Shop</a><a>Latest Blog</a><a>Reviews</a><a>Coupon Codes</a><a>Information</a>
  </nav>
</header>
<div class="brand">Verdant<br>Notes</div>

<section class="hero">
  <div class="hero-photo" role="img" aria-label="Cannabis seedling growing from soil beside wild mushrooms in warm sunlight"></div>
  <h1 class="hero-title">Verdant Notes</h1>
  <p class="hero-lead">Lorem ipsum dolor sit amet, consectetur adipiscing elit, sed do eiusmod tempor incididunt ut labore et dolore magna aliqua.</p>
  <a class="btn">Get Started
    <svg class="btn-ico" viewBox="0 0 14 14"><circle cx="7" cy="7" r="7" fill="#fff"/><path d="M6 4l3 3-3 3" stroke="#8cb83f" stroke-width="2" fill="none"/></svg></a>
  <div class="dots"><i></i><i></i><i class="on"></i><i></i><i></i></div>
</section>

<!-- deals -->
<div class="deal" style="left:112px">
  <div class="deal-photo" role="img" aria-label="Cannabis buds spilling from a glass jar" style="background:linear-gradient(135deg,#8a8a6e,#55603a 60%,#3b3f2a)"></div>
  <div class="deal-label">Concentrate Deals <svg class="btn-ico" viewBox="0 0 14 14"><circle cx="7" cy="7" r="7" fill="#fff"/><path d="M6 4l3 3-3 3" stroke="#333" stroke-width="2" fill="none"/></svg></div>
</div>
<div class="deal active" style="left:442px">
  <div class="deal-photo" role="img" aria-label="Hand holding a medical cannabis bottle under green tint" style="background:linear-gradient(135deg,#b4d47a,#a5c865)"></div>
  <div class="frame"></div>
  <div class="deal-label">Cannabis Deals <svg class="btn-ico" viewBox="0 0 14 14"><circle cx="7" cy="7" r="7" fill="#fff"/><path d="M6 4l3 3-3 3" stroke="#8cb83f" stroke-width="2" fill="none"/></svg></div>
</div>
<div class="deal" style="left:773px">
  <div class="deal-photo" role="img" aria-label="Laptop screen showing a promo code offer" style="background:linear-gradient(135deg,#c9bfb5 0%,#e2582a 45%,#a52a14 70%,#3a3a3a 100%)"></div>
  <div class="deal-label">Coupon Codes <svg class="btn-ico" viewBox="0 0 14 14"><circle cx="7" cy="7" r="7" fill="#fff"/><path d="M6 4l3 3-3 3" stroke="#333" stroke-width="2" fill="none"/></svg></div>
</div>

<!-- info row -->
<div class="panel" style="left:112px">
  <div class="panel-photo" role="img" aria-label="Dark cannabis leaves background"></div>
  <div class="panel-body" style="padding-top:52px">
    <h2>About Us</h2>
    <p style="margin-top:10px">sed quia consequuntur magni dolores eos qui ratione voluptatem sequi nesciunt. Neque porro quisquam est, qui dolorem ipsum quia dolor sit amet, consectetur.</p>
    <a class="btn">Read More <svg class="btn-ico" viewBox="0 0 14 14"><circle cx="7" cy="7" r="7" fill="#fff"/><path d="M6 4l3 3-3 3" stroke="#8cb83f" stroke-width="2" fill="none"/></svg></a>
  </div>
</div>
<article class="post" style="left:358px;top:1065px">
  <div class="post-photo" role="img" aria-label="Hand holding a cannabis oil dropper bottle among leaves" style="background:linear-gradient(135deg,#5c8a2a,#c9b43a 55%,#e3c86a)"></div>
  <h3>Lorem Ipsum Dolor</h3>
  <p style="margin-top:26px">Sed ut perspiciatis unde omniste natus error sit volupaccusantium doloremque laudantium, totam rem aperiam, eaque ipsa quae ab illo inventore veritatis et quasi architecto beatae vitae dicta sunt explicabo.</p>
  <a class="read">Read More <span>»</span></a>
</article>
<article class="post" style="left:604px;top:1065px">
  <div class="post-photo" role="img" aria-label="Scientist inspecting cannabis plants in a lab" style="background:linear-gradient(135deg,#6a7d8a,#c8d0d6 45%,#4a7a34)"></div>
  <h3>Lorem Ipsum Dolor</h3>
  <p style="margin-top:26px">Sed ut perspiciatis unde omniste natus error sit volupaccusantium doloremque laudantium, totam rem aperiam, eaque ipsa quae ab illo inventore veritatis et quasi architecto beatae vitae dicta sunt explicabo.</p>
  <a class="read">Read More <span>»</span></a>
</article>
<div class="panel" style="left:851px">
  <div class="panel-photo" role="img" aria-label="Dark background with jar of cannabis" style="background:linear-gradient(180deg,#2d2c28,#3a3328 60%,#2a2a26)"></div>
  <div class="panel-body" style="padding-top:36px">
    <h2>Why Choose Us</h2>
    <p style="margin-top:14px">sed quia consequuntur magni dolores eos qui ratione voluptatem sequi nesciunt. Neque porro quisquam est, qui dolorem ipsum quia dolor sit amet, consectetur.</p>
    <a class="btn">Read More <svg class="btn-ico" viewBox="0 0 14 14"><circle cx="7" cy="7" r="7" fill="#fff"/><path d="M6 4l3 3-3 3" stroke="#8cb83f" stroke-width="2" fill="none"/></svg></a>
  </div>
</div>

<!-- promo banner -->
<svg class="promo" viewBox="0 0 978 181" role="img" aria-label="Advertisement: Cannabis and Mushroom, get 10 percent off">
  <rect width="978" height="181" fill="#fff"/>
  <polygon points="0,0 620,0 535,181 0,181" fill="#2a2a2a"/>
  <polygon points="0,0 150,0 0,92" fill="#3f9a1e"/>
  <polygon points="150,0 165,0 0,100 0,92" fill="#fff"/>
  <polygon points="608,0 628,0 543,181 410,181 520,80" fill="#8cb83f"/>
  <rect x="585" y="18" width="155" height="150" fill="#b0895a" opacity=".35"/>
  <rect x="896" y="0" width="82" height="181" fill="#8cb83f"/>
  <rect x="890" y="0" width="6" height="181" fill="#2a2a2a"/>
  <circle cx="893" cy="93" r="55" fill="#fff"/>
  <text x="893" y="89" text-anchor="middle" font-family="Montserrat,sans-serif" font-weight="600" font-size="13" fill="#222">Verdant</text>
  <text x="893" y="105" text-anchor="middle" font-family="Montserrat,sans-serif" font-weight="600" font-size="13" fill="#222">Notes</text>
  <circle cx="498" cy="90" r="60" fill="#8cb83f"/>
  <circle cx="498" cy="90" r="53" fill="none" stroke="#a8cf63" stroke-width="2"/>
  <g font-family="Montserrat,sans-serif" font-weight="600" fill="#fff" text-anchor="middle" font-size="24">
    <text x="498" y="68">Get</text><text x="498" y="99">10 %</text><text x="498" y="130">OFF</text>
  </g>
  <g font-family="Montserrat,sans-serif" font-weight="600" fill="#fff" text-anchor="middle" font-size="44">
    <text x="230" y="77">Cannabis &amp;</text><text x="245" y="133">Mushroom</text>
  </g>
</svg>

<!-- blog grid -->
<article class="post" style="left:112px;top:1966px">
  <div class="post-photo" role="img" aria-label="Cannabis cream jar with leaves" style="background:linear-gradient(135deg,#d8d6c8,#6e8a3a 55%,#8a7a5a)"><div class="post-date">FEB<br>2020</div></div>
  <h3>Lorem Ipsum Dolor</h3><div class="rule"></div>
  <p>Sed ut perspiciatis unde omniste natus error sit volupaccusantium doloremque laudantium, totam rem aperiam, eaque ipsa quae ab illo inventore veritatis et quasi architecto beatae vitae dicta sunt explicabo.</p>
  <a class="read">Read More <span>»</span></a>
</article>
<article class="post" style="left:358px;top:1966px">
  <div class="post-photo" role="img" aria-label="Basket of foraged mushrooms in a forest" style="background:linear-gradient(135deg,#d9c89a,#8a6a3a 55%,#5a6a2a)"><div class="post-date">FEB<br>2020</div></div>
  <h3>Lorem Ipsum Dolor</h3><div class="rule"></div>
  <p>Sed ut perspiciatis unde omniste natus error sit volupaccusantium doloremque laudantium, totam rem aperiam, eaque ipsa quae ab illo inventore veritatis et quasi architecto beatae vitae dicta sunt explicabo.</p>
  <a class="read">Read More <span>»</span></a>
</article>
<article class="post" style="left:604px;top:1966px">
  <div class="post-photo" role="img" aria-label="Oil dropper over a cup of tea" style="background:linear-gradient(135deg,#9aa6ac,#cfd6d8 50%,#3d7a8a)"><div class="post-date">FEB<br>2020</div></div>
  <h3>Lorem Ipsum Dolor</h3><div class="rule"></div>
  <p>Sed ut perspiciatis unde omniste natus error sit volupaccusantium doloremque laudantium, totam rem aperiam, eaque ipsa quae ab illo inventore veritatis et quasi architecto beatae vitae dicta sunt explicabo.</p>
  <a class="read">Read More <span>»</span></a>
</article>
<article class="post" style="left:112px;top:2515px">
  <div class="post-photo" role="img" aria-label="Hemp oil bottles with seeds and leaves" style="background:linear-gradient(135deg,#4a6a2a,#c8c24a 50%,#8a7a4a)"><div class="post-date">FEB<br>2020</div></div>
  <h3>Lorem Ipsum Dolor</h3><div class="rule"></div>
  <p>Sed ut perspiciatis unde omniste natus error sit volupaccusantium doloremque laudantium, totam rem aperiam, eaque ipsa quae ab illo inventore veritatis et quasi architecto beatae vitae dicta sunt explicabo.</p>
  <a class="read">Read More <span>»</span></a>
</article>
<article class="post" style="left:358px;top:2515px">
  <div class="post-photo" role="img" aria-label="Assorted wild mushrooms on a table" style="background:linear-gradient(135deg,#6a4a2a,#a8804a 50%,#3a4a2a)"><div class="post-date">FEB<br>2020</div></div>
  <h3>Lorem Ipsum Dolor</h3><div class="rule"></div>
  <p>Sed ut perspiciatis unde omniste natus error sit volupaccusantium doloremque laudantium, totam rem aperiam, eaque ipsa quae ab illo inventore veritatis et quasi architecto beatae vitae dicta sunt explicabo.</p>
  <a class="read">Read More <span>»</span></a>
</article>
<article class="post" style="left:604px;top:2515px">
  <div class="post-photo" role="img" aria-label="Glass pipe with cannabis buds on dark surface" style="background:linear-gradient(135deg,#3a3a34,#5a5a40 50%,#2a2a28)"><div class="post-date">FEB<br>2020</div></div>
  <h3>Lorem Ipsum Dolor</h3><div class="rule"></div>
  <p>Sed ut perspiciatis unde omniste natus error sit volupaccusantium doloremque laudantium, totam rem aperiam, eaque ipsa quae ab illo inventore veritatis et quasi architecto beatae vitae dicta sunt explicabo.</p>
  <a class="read">Read More <span>»</span></a>
</article>

<!-- trending -->
<aside class="trending">
  <h2>Trending Posts</h2>
  <div class="trend"><div class="trend-photo" role="img" aria-label="Cannabis cream" style="background:linear-gradient(135deg,#e0dccd,#8a8a5a)"></div><div class="trend-text">Lorem ipsum dolor sit amet, consectetur adipiscing elit, sed do<small>10 Feb 2020</small></div></div>
  <div class="trend"><div class="trend-photo" role="img" aria-label="Pre-rolled joints" style="background:linear-gradient(135deg,#e8e8e0,#4a6a2a)"></div><div class="trend-text">Lorem ipsum dolor sit amet, consectetur adipiscing elit, sed do<small>10 Feb 2020</small></div></div>
  <div class="trend"><div class="trend-photo" role="img" aria-label="Oil bottles and leaves" style="background:linear-gradient(135deg,#e6dcc0,#6a8a3a)"></div><div class="trend-text">Lorem ipsum dolor sit amet, consectetur adipiscing elit, sed do<small>10 Feb 2020</small></div></div>
  <div class="trend"><div class="trend-photo" role="img" aria-label="Hand holding a cannabis bud" style="background:linear-gradient(135deg,#d8c8c0,#5a7a3a)"></div><div class="trend-text">Lorem ipsum dolor sit amet, consectetur adipiscing elit, sed do<small>10 Feb 2020</small></div></div>
  <div class="trend"><div class="trend-photo" role="img" aria-label="Cannabis balm with leaf" style="background:linear-gradient(135deg,#c8c08a,#3a5a2a)"></div><div class="trend-text">Lorem ipsum dolor sit amet, consectetur adipiscing elit, sed do<small>10 Feb 2020</small></div></div>
</aside>

<nav class="pager"><span>1</span><span>2</span><span>3</span><span class="next">Next ›</span></nav>

<footer class="site-footer" role="contentinfo">
  <div class="social"><i></i><i></i><i></i><i></i></div>
  <nav class="foot-nav"><a>Home</a><a>About Us</a><a>Shop</a><a>Latest Blog</a><a>Reviews</a><a>Coupon Codes</a><a>Information</a></nav>
  <p class="copy">© 2020 Verdant Notes. All Rights reserved</p>
</footer>

</body>
</html>
```